Trading Company needs a business card design, letter head design and email signature

We need a double-sided business card design, letter head design and an email signature. We have a logo design.

Possible Tag Lines:
• “Connecting Worlds, Building Excellence.”
• “Global Sourcing, Local Excellence.”
• “Bridging Borders, Building Quality.”
• “Worldwide Partnerships, Superior Goods.”
• “Where Quality Meets Affordability”

Services Offered:
Procurement
Fabrication
Distribution
Logistics
Import/Export

Requirements
Must have
• Nice quality double sided Business Card design, Letterhead design needs to be A4
Nice to have
• possible ideas on tag lines

```html
<!DOCTYPE html>
<html lang="en">
<head>
<meta charset="utf-8">
<title>Vantrade Business Card</title>
<link href="https://fonts.googleapis.com/css2?family=Roboto:wght@400;700;900&family=Michroma&display=swap" rel="stylesheet">
<style>
  :root {
    --backdrop: #2b2b2d;
    --card-dark: #0d0d0f;
    --card-dark-edge: #1c1c20;
    --card-light: #ffffff;
    --brand-red: #e3262b;
    --brand-grey: #58595b;
    --text-dark: #3a3a3c;
    --text-light: #f2f2f2;
    --divider-dark: #6a6a70;
    --divider-light: #b8b8bc;
  }
  * { box-sizing: border-box; margin: 0; padding: 0; }
  html, body { width: 1200px; height: 904px; overflow: hidden; }
  body {
    background: var(--backdrop);
    font-family: "Roboto", Arial, sans-serif;
    position: relative;
  }
  .card {
    position: absolute;
    left: 260px;
    width: 680px;
    height: 389px;
    box-shadow: 0 10px 30px rgba(0,0,0,.45);
    display: flex;
    align-items: center;
  }
  .card--back {
    top: 40px;
    background: linear-gradient(120deg, var(--card-dark) 0%, var(--card-dark-edge) 55%, var(--card-dark) 100%);
  }
  .card--front {
    top: 475px;
    background: var(--card-light);
  }
  .brand {
    width: 340px;
    display: flex;
    flex-direction: column;
    align-items: center;
    padding-left: 30px;
  }
  .brand__mark {
    display: flex;
    align-items: center;
    gap: 12px;
  }
  .brand__square {
    width: 30px;
    height: 30px;
    background: var(--brand-red);
  }
  .brand__name {
    font-weight: 900;
    font-size: 44px;
    letter-spacing: 1px;
    color: var(--brand-red);
    text-transform: uppercase;
  }
  .brand__tagline {
    margin-top: 8px;
    font-weight: 700;
    font-size: 11px;
    letter-spacing: 1.2px;
    text-transform: uppercase;
  }
  .card--back .brand__tagline { color: var(--brand-grey); }
  .card--front .brand__tagline { color: var(--brand-grey); }
  .divider {
    width: 1px;
    height: 140px;
    margin: 0 34px 0 10px;
    transform: rotate(-20deg);
  }
  .card--back .divider { background: var(--divider-dark); }
  .card--front .divider { background: var(--divider-light); }
  .services__title {
    font-family: "Michroma", "Roboto", sans-serif;
    color: var(--brand-red);
    font-size: 17px;
    letter-spacing: 1px;
    margin-bottom: 8px;
  }
  .services__list { list-style: none; }
  .services__item {
    color: var(--text-light);
    font-size: 22px;
    line-height: 1.22;
    display: flex;
    align-items: center;
    gap: 10px;
  }
  .services__item::before {
    content: "";
    width: 7px; height: 7px;
    border-radius: 50%;
    background: var(--brand-red);
  }
  .contact { color: var(--text-dark); }
  .contact__name {
    font-size: 22px;
    font-weight: 700;
    letter-spacing: .5px;
    text-transform: uppercase;
  }
  .contact__first { color: var(--brand-red); }
  .contact__last { color: var(--brand-grey); }
  .contact__role { font-size: 18px; margin-bottom: 16px; }
  .contact__address { font-size: 18px; line-height: 1.2; margin-bottom: 10px; }
  .contact__line {
    display: flex;
    align-items: center;
    gap: 10px;
    font-size: 19px;
    line-height: 1.25;
  }
  .contact__icon { width: 17px; height: 17px; flex: none; }
</style>
</head>
<body>
  <section class="card card--back">
    <div class="brand">
      <div class="brand__mark">
        <span class="brand__square"></span>
        <span class="brand__name">Vantrade</span>
      </div>
      <p class="brand__tagline">Global Sourcing, Local Excellence</p>
    </div>
    <span class="divider"></span>
    <div class="services">
      <h2 class="services__title">SERVICES OFFERED:</h2>
      <ul class="services__list">
        <li class="services__item">Procurement</li>
        <li class="services__item">Fabrication</li>
        <li class="services__item">Distribution</li>
        <li class="services__item">Logistics</li>
        <li class="services__item">Import/Export</li>
      </ul>
    </div>
  </section>

  <section class="card card--front">
    <div class="brand">
      <div class="brand__mark">
        <span class="brand__square"></span>
        <span class="brand__name">Vantrade</span>
      </div>
      <p class="brand__tagline">Global Sourcing, Local Excellence</p>
    </div>
    <span class="divider"></span>
    <div class="contact">
      <p class="contact__name"><span class="contact__first">Dana</span> <span class="contact__last">Whitford</span></p>
      <p class="contact__role">Founder &amp; CEO</p>
      <p class="contact__address">48 Harbor Lane Suite<br>2 Dover, MA 02030</p>
      <p class="contact__line">
        <svg class="contact__icon" viewBox="0 0 24 24"><path fill="#e3262b" d="M6.6 10.8a15 15 0 0 0 6.6 6.6l2.2-2.2c.3-.3.7-.4 1-.2 1.1.4 2.3.6 3.6.6.6 0 1 .4 1 1V20c0 .6-.4 1-1 1A17 17 0 0 1 3 4c0-.6.4-1 1-1h3.5c.6 0 1 .4 1 1 0 1.3.2 2.5.6 3.6.1.3 0 .7-.2 1z"/></svg>
        (555) 014-2290
      </p>
      <p class="contact__line">
        <svg class="contact__icon" viewBox="0 0 24 24"><rect x="2" y="5" width="20" height="14" fill="none" stroke="#e3262b" stroke-width="2"/><path d="M2 5l10 8 10-8" fill="none" stroke="#e3262b" stroke-width="2"/></svg>
        info@vantrademail.com
      </p>
      <p class="contact__line">
        <svg class="contact__icon" viewBox="0 0 24 24"><g fill="none" stroke="#e3262b" stroke-width="2"><circle cx="12" cy="12" r="10"/><ellipse cx="12" cy="12" rx="4" ry="10"/><path d="M2 12h20"/></g></svg>
        www.vantradeweb.com
      </p>
    </div>
  </section>
</body>
</html>
```